Harborview Optical -Window Poster (Optometrist)

We are an optometry practice and we need a poster for a new store promotion for our window highlighting we now also sell 2 pairs of glasses as a package deal. The size will be 1300mm width x 1900mm height

The artwork will be displayed as a fabric banner in our shop window. We have 7 other banners with different services our business provides. The words needs to standout for passers by and the cars stopped at the traffic lights out front of our business. We already have signs with our logos phone number etc. so we won't need them included in the poster.

It would need to include the following information.

Two pair packages now available*

*Conditions apply

The artwork will be displayed as a fabric banner in our shop window. We have 7 other banners with different services our business provides. The words needs to standout for passers by and the cars stopped at the traffic lights out front of our business. We already have signs with our logos phone number etc. so we won't need them included in the poster. Thank you for your work it's amazing Added Saturday, February 18, 2017

The artwork will be displayed as a fabric banner in our shop window. We have 7 other banners with different services our business provides. The words needs to standout for passers by and the cars stopped at the traffic lights out front of our business. We already have signs with our logos phone number etc. so we won't need them included in the poster. Added Saturday, February 18, 2017

Target Market(s)

Cars driving past and stopped at traffic lights outside our store.

Industry/Entity Type

Optician

Requirements
Must have
• Poster must say:
• Two pair packages now available*
• *Conditions apply

```html
<!DOCTYPE html>
<html lang="en">
<head>
<meta charset="UTF-8">
<title>Harborview Optical – Two Pair Packages Window Poster</title>
<link rel="stylesheet" href="https://fonts.googleapis.com/css2?family=Anton&family=Lora:ital,wght@1,700&family=Righteous&family=Yellowtail&display=swap">
<style>
  :root {
    --poster-black: #070707;
    --retina-red: #6e241c;
    --retina-deep: #4e1712;
    --retina-glow: #8a3a26;
    --headline-white: #f4f2ee;
    --headline-shadow: #2a0b08;
    --package-orange: #f0952a;
    --conditions-yellow: #f5ee10;
    --streak-blue: rgba(120, 150, 190, 0.25);
  }
  html, body {
    margin: 0;
    padding: 0;
    width: 962px;
    height: 1200px;
    overflow: hidden;
    background: var(--poster-black);
  }
  .poster {
    position: relative;
    width: 962px;
    height: 1200px;
    background: var(--poster-black);
    overflow: hidden;
  }
  .light-streaks {
    position: absolute;
    inset: 0;
  }
  .retina {
    position: absolute;
    left: 16px;
    top: 174px;
    width: 927px;
    height: 790px;
    border-radius: 50%;
    background: radial-gradient(circle at 15% 45%, var(--retina-glow) 0%, var(--retina-red) 30%, var(--retina-red) 65%, var(--retina-deep) 100%);
  }
  .offer {
    position: absolute;
    left: 0;
    right: 0;
    margin: 0;
    text-align: center;
    line-height: 1;
    white-space: nowrap;
  }
  .offer-lead {
    top: 326px;
    padding-left: 62px;
    font-family: "Lora", Georgia, serif;
    font-style: italic;
    font-weight: 700;
    font-size: 64px;
    letter-spacing: 4px;
    color: var(--headline-white);
  }
  .offer-title {
    top: 441px;
    font-family: "Anton", Impact, sans-serif;
    font-weight: 400;
    font-size: 152px;
    letter-spacing: 14px;
    color: var(--headline-white);
    text-shadow: 5px 5px 0 var(--headline-shadow);
    transform: scaleX(1.18);
    transform-origin: 473px 50%;
  }
  .offer-subtitle {
    top: 630px;
    padding-left: 28px;
    font-family: "Righteous", sans-serif;
    font-weight: 400;
    font-size: 88px;
    letter-spacing: 12px;
    color: var(--package-orange);
  }
  .offer-rule {
    position: absolute;
    left: 338px;
    top: 745px;
    width: 341px;
    height: 3px;
    background: linear-gradient(90deg, transparent, var(--headline-white) 20%, var(--headline-white) 80%, transparent);
  }
  .conditions {
    position: absolute;
    left: 0;
    right: 0;
    top: 1012px;
    margin: 0;
    padding-left: 26px;
    text-align: center;
    line-height: 1;
    white-space: nowrap;
    font-family: "Yellowtail", cursive;
    font-size: 80px;
    letter-spacing: 4px;
    color: var(--conditions-yellow);
  }
</style>
</head>
<body>
  <main class="poster">
    <svg class="light-streaks" width="962" height="1200" viewBox="0 0 962 1200" aria-hidden="true">
      <rect x="0" y="52" width="360" height="4" fill="var(--streak-blue)"/>
      <rect x="500" y="172" width="462" height="5" fill="var(--streak-blue)"/>
      <rect x="0" y="176" width="130" height="3" fill="rgba(255,255,255,0.3)"/>
      <rect x="0" y="1008" width="490" height="5" fill="var(--streak-blue)"/>
      <rect x="860" y="360" width="102" height="3" fill="rgba(255,255,255,0.3)"/>
    </svg>

    <div class="retina" role="img" aria-label="Close-up photograph of a retina with branching blood vessels, in deep red tones"></div>

    <p class="offer offer-lead">now available*</p>
    <h1 class="offer offer-title">TWO PAIR</h1>
    <h2 class="offer offer-subtitle">PACKAGES</h2>
    <div class="offer-rule"></div>

    <p class="conditions">*Conditions Apply</p>
  </main>
</body>
</html>
```